Veldmark Supplies Business Card

Professional business card that stand out to our potential customers. Front and back with clean modern design

Industry/Entity Type

Oil and gas

Contact Information for Business Card

Name, address, website , office phone and cell number

Requirements
Must have
• Editable files for each employee

```html
<!DOCTYPE html>
<html lang="en">
<head>
<meta charset="utf-8">
<title>Veldmark Supplies Business Card</title>
<link rel="stylesheet" href="https://fonts.googleapis.com/css2?family=Arimo:wght@400;700&display=swap">
<style>
  :root {
    --brand-red: #e8201f;
    --brand-teal: #03abd0;
    --mid-grey: #949a98;
    --ink: #1d1d1f;
    --paper: #ffffff;
    --backdrop: #d3d4d6;
  }
  * { margin: 0; padding: 0; box-sizing: border-box; }
  html, body {
    width: 900px; height: 1200px; overflow: hidden;
    background: var(--backdrop);
    font-family: "Arimo", Arial, sans-serif;
  }
  .canvas { position: relative; width: 900px; height: 1200px; }

  .card {
    position: absolute; left: 134px; width: 632px; height: 364px;
    overflow: hidden;
  }
  .card--front {
    top: 210px;
    background: linear-gradient(90deg, var(--brand-red) 4%, #d6573f 25%, #a98a7d 47%, var(--mid-grey) 60%, #6fb0bf 78%, #1ebad8 100%);
  }
  .card--back { top: 624px; background: var(--paper); }

  .front-brand {
    position: absolute; left: 0; right: 0; top: 164px;
    display: flex; justify-content: center; align-items: center; gap: 12px;
    color: var(--paper); font-weight: 700; font-size: 30px; letter-spacing: 0.5px;
  }
  .front-brand .brand-square { width: 22px; height: 22px; background: var(--paper); }

  .back-brand {
    position: absolute; left: 40px; width: 260px; top: 170px;
    display: flex; justify-content: center; align-items: center; gap: 9px;
    color: var(--brand-red); font-weight: 700; font-size: 22px;
  }
  .back-brand .brand-square { width: 16px; height: 16px; background: var(--brand-red); }

  .divider { position: absolute; left: 316px; width: 2px; }
  .divider--top { top: 98px; height: 38px; background: var(--brand-red); }
  .divider--mid { top: 140px; height: 88px; width: 4px; left: 315px; background: var(--brand-teal); }
  .divider--bottom { top: 232px; height: 38px; background: var(--brand-red); }

  .contact { position: absolute; left: 346px; top: 96px; color: var(--ink); font-size: 15.5px; }
  .contact__name { font-size: 25px; font-weight: 700; line-height: 1; margin-bottom: 8px; }
  .contact__name .first { color: var(--brand-red); }
  .contact__name .last { color: var(--brand-teal); }
  .contact__role { line-height: 1; margin-bottom: 10px; }
  .contact__address { line-height: 20px; margin-bottom: 6px; }
  .contact__row { display: flex; align-items: center; gap: 9px; height: 25.5px; }
  .contact__row svg { width: 15px; height: 15px; fill: var(--brand-teal); flex: none; }
  .contact__phone { letter-spacing: 2.6px; }

  .base-band { position: absolute; left: 0; bottom: 0; width: 632px; height: 13px; }
</style>
</head>
<body>
<div class="canvas">
  <section class="card card--front" aria-label="Card front">
    <div class="front-brand"><span class="brand-square"></span><span>Veldmark Supplies</span></div>
  </section>

  <section class="card card--back" aria-label="Card back">
    <div class="back-brand"><span class="brand-square"></span><span>Veldmark Supplies</span></div>

    <div class="divider divider--top"></div>
    <div class="divider divider--mid"></div>
    <div class="divider divider--bottom"></div>

    <div class="contact">
      <p class="contact__name"><span class="first">Ravesh</span> <span class="last">Amrin</span></p>
      <p class="contact__role">CEO</p>
      <p class="contact__address">417 N.Ridgeline Suite 5<br>Cardell, Tx 79842</p>
      <p class="contact__row">
        <svg viewBox="0 0 24 24" aria-hidden="true"><path d="M6.6 10.8a15.1 15.1 0 0 0 6.6 6.6l2.2-2.2a1 1 0 0 1 1-.25 11.4 11.4 0 0 0 3.6.57 1 1 0 0 1 1 1V20a1 1 0 0 1-1 1A17 17 0 0 1 3 4a1 1 0 0 1 1-1h3.5a1 1 0 0 1 1 1c0 1.25.2 2.45.57 3.57a1 1 0 0 1-.25 1z"/></svg>
        <span class="contact__phone">(555)014-0372</span>
      </p>
      <p class="contact__row">
        <svg viewBox="0 0 24 24" aria-hidden="true"><path d="M2 5h20v14H2z M3.5 6.5l8.5 6.5 8.5-6.5" fill="none" stroke="#03abd0" stroke-width="0"/><path d="M2 5h20l-10 7.5z"/><path d="M2 7l7 5.5L2 18z M22 7l-7 5.5L22 18z M10.3 13.5L12 14.8l1.7-1.3L21 19H3z"/></svg>
        <span>sales@veldmarksupplies.com</span>
      </p>
      <p class="contact__row">
        <svg viewBox="0 0 24 24" aria-hidden="true"><circle cx="12" cy="12" r="9.5" fill="none" stroke="#03abd0" stroke-width="2"/><ellipse cx="12" cy="12" rx="4" ry="9.5" fill="none" stroke="#03abd0" stroke-width="1.6"/><path d="M2.5 12h19M4 7h16M4 17h16" stroke="#03abd0" stroke-width="1.6"/></svg>
        <span>www.veldmarksupplies.com</span>
      </p>
    </div>

    <svg class="base-band" viewBox="0 0 632 13" aria-hidden="true">
      <polygon points="0,0 324,0 319,13 0,13" fill="#e8201f"/>
      <polygon points="328,0 632,0 632,13 323,13" fill="#03abd0"/>
    </svg>
  </section>
</div>
</body>
</html>
```